Norrell Advisory WA Business Card

Create an interesting, eye catching and colourful two sided business card. We are a business consulting operation assisting SME's improve all areas of their business. We provide consulting services to assist SME's to create a culture of continuous improvement, making a positive difference in the business. Our tag line is Small changes, big rewards. We want to create a well recognised, innovative brand that can be continued throughout our website, social media and email correspondence.

Target Market(s)

Small to Medium Enterprise Business Owners

Industry/Entity Type

Business Consultant

Contact Information for Business Card

Name of Business: Norrell Advisory - Small Changes Big Rewards
Derek Holloway Ph 0407385510 Megan Holloway Ph 0407913847
Email norrelladvisorywa@mailbox-example.com
Web address TBA
FaceBook page TBA

BACKSIDE OF CARD

Providing assistance with:

• Organisation & Efficiency
• Revenue generation & Marketing
• Financial Management
• Production quality & delivery
• Systems & Process documentation
• Exit Strategy

Font styles to use
Other font styles liked:
• Calibri

Colors

Designer to choose colors to be used in the design.

Requirements
Must have
• Calibri font

```html
<!DOCTYPE html>
<html lang="en">
<head>
<meta charset="utf-8">
<title>Norrell Advisory WA Business Card</title>
<link rel="stylesheet" href="https://fonts.googleapis.com/css2?family=Open+Sans:ital,wght@0,400;0,600;0,700;1,600&display=swap">
<style>
  :root {
    --page-bg: #e4e4e4;
    --card-front: #ffffff;
    --card-back: #1c1c1c;
    --ink-dark: #555555;
    --ink-light: #e6e6e6;
    --puzzle-orange: #f7a733;
    --puzzle-yellow: #fdd835;
    --puzzle-blue: #4aa8d8;
    --puzzle-red: #e8503a;
    --puzzle-green: #8cc63f;
  }
  * { box-sizing: border-box; margin: 0; padding: 0; }
  html, body {
    width: 1125px; height: 1200px; overflow: hidden;
    background: var(--page-bg);
    font-family: "Open Sans", Calibri, sans-serif;
  }
  .card {
    position: absolute; left: 171px; width: 826px; height: 471px;
    border-radius: 22px; overflow: hidden;
  }
  .card--front { top: 106px; background: var(--card-front); }
  .card--back { top: 639px; background: var(--card-back); }

  .front-artwork {
    position: absolute; left: 420px; top: 0; right: 0; bottom: 0;
    background:
      radial-gradient(circle at 30% 30%, var(--puzzle-yellow) 0, transparent 38%),
      radial-gradient(circle at 78% 12%, var(--puzzle-blue) 0, transparent 30%),
      radial-gradient(circle at 92% 48%, var(--puzzle-red) 0, transparent 30%),
      radial-gradient(circle at 65% 75%, var(--puzzle-green) 0, transparent 40%),
      linear-gradient(120deg, var(--puzzle-orange), var(--puzzle-yellow) 45%, var(--puzzle-green));
    opacity: 0.9;
    -webkit-mask-image: linear-gradient(to right, transparent 0, #000 22%);
    mask-image: linear-gradient(to right, transparent 0, #000 22%);
  }

  .contact-people { position: absolute; left: 63px; top: 178px; color: var(--ink-dark); }
  .person { margin-bottom: 18px; }
  .person__name { font-size: 32px; font-weight: 700; line-height: 1; text-transform: uppercase; }
  .person__phone { font-size: 25px; font-weight: 700; line-height: 1.1; margin-top: 2px; }

  .contact-links { position: absolute; left: 63px; top: 353px; list-style: none; color: var(--ink-dark); }
  .contact-links li { display: flex; align-items: center; gap: 9px; font-size: 16px; line-height: 25px; }
  .contact-links svg { width: 15px; height: 15px; flex: none; }

  .back-brand { position: absolute; left: 0; width: 443px; top: 268px; text-align: center; }
  .back-brand__name { color: var(--ink-light); font-size: 30px; font-weight: 700; line-height: 1; text-transform: uppercase; }

  .services { position: absolute; left: 417px; top: 134px; color: var(--ink-light); }
  .services__title { font-size: 26px; font-weight: 600; font-style: italic; line-height: 1.2; margin-bottom: 6px; }
  .services__list { list-style: none; }
  .services__list li { font-size: 18px; line-height: 24.8px; padding-left: 22px; position: relative; }
  .services__list li::before {
    content: ""; position: absolute; left: 5px; top: 10px;
    width: 6px; height: 6px; border-radius: 50%; background: var(--ink-light);
  }
</style>
</head>
<body>
  <section class="card card--front">
    <div class="front-artwork" role="img" aria-label="Colourful interlocking puzzle piece artwork in orange, yellow, blue, red and green"></div>

    <div class="contact-people">
      <div class="person">
        <p class="person__name">Derek Holloway</p>
        <p class="person__phone">0407385510</p>
      </div>
      <div class="person">
        <p class="person__name">Megan Holloway</p>
        <p class="person__phone">0407913847</p>
      </div>
    </div>

    <ul class="contact-links">
      <li>
        <svg viewBox="0 0 16 16" aria-hidden="true"><rect x="1" y="1" width="14" height="14" rx="1.5" fill="var(--ink-dark)"/></svg>
        norrelladvisorywa
      </li>
      <li>
        <svg viewBox="0 0 16 16" aria-hidden="true"><rect x="1" y="3" width="14" height="10" fill="var(--ink-dark)"/><path d="M1.5 3.5 L8 9 L14.5 3.5" fill="none" stroke="#fff" stroke-width="1.3"/></svg>
        norrelladvisorywa@mailbox-example.com
      </li>
      <li>
        <svg viewBox="0 0 16 16" aria-hidden="true"><circle cx="8" cy="8" r="7" fill="var(--ink-dark)"/><path d="M1 8 H15 M8 1 C4.5 4 4.5 12 8 15 M8 1 C11.5 4 11.5 12 8 15" fill="none" stroke="#fff" stroke-width="1"/></svg>
        norrelladvisorywa.com
      </li>
    </ul>
  </section>

  <section class="card card--back">
    <div class="back-brand">
      <p class="back-brand__name">Norrell Advisory</p>
    </div>

    <div class="services">
      <h2 class="services__title">Providing assistance with</h2>
      <ul class="services__list">
        <li>Organisation &amp; Efficiency</li>
        <li>Revenue generation &amp; Marketing</li>
        <li>Financial Management</li>
        <li>Production quality &amp; delivery</li>
        <li>Systems &amp; Process documentation</li>
        <li>Exit Strategy</li>
      </ul>
    </div>
  </section>
</body>
</html>
```